Corporate Business Card

Very professional, Modern, Not to busy, include phone address email, website
(253) 617-4930, 18761 52nd Avenue S, Kent, WA 98047, martin@plumlinegroup.com, varkoworks.com

Target Market(s)

Manufacturing

Industry/Entity Type

Aero, machining, manufacturing, Off road racing

Contact Information for Business Card

Phone, address email, website

```html
<!DOCTYPE html>
<html lang="en">
<head>
<meta charset="utf-8">
<title>Varko Works — Business Card</title>
<link href="https://fonts.googleapis.com/css2?family=Montserrat:wght@500;700&display=swap" rel="stylesheet">
<style>
  :root {
    --bg: #2b2b2b;
    --red: #d3202b;
    --navy: #1c3370;
    --white: #ffffff;
    --ink: #1a1a1a;
  }
  html, body {
    margin: 0;
    width: 1200px;
    height: 960px;
    overflow: hidden;
    background: var(--bg);
    font-family: "Montserrat", sans-serif;
  }
  .canvas { position: relative; width: 1200px; height: 960px; }
  .card {
    position: absolute;
    width: 560px;
    height: 320px;
    border-radius: 2px;
    overflow: hidden;
    box-shadow: 0 14px 30px rgba(0,0,0,0.45);
  }
  .card-front { left: 70px; top: 90px; background: var(--red); }
  .card-back { left: 570px; top: 520px; background: var(--white); }

  .brand-name {
    position: absolute;
    font-weight: 700;
    letter-spacing: 1px;
    white-space: nowrap;
    margin: 0;
  }
  .card-front .brand-name {
    color: var(--white);
    font-size: 54px;
    right: 60px;
    top: 120px;
  }
  .card-back .brand-name {
    color: var(--navy);
    font-size: 34px;
    right: 36px;
    top: 30px;
  }

  .wave { position: absolute; left: 0; top: 0; }

  .contact {
    position: absolute;
    left: 46px;
    top: 100px;
    color: var(--ink);
    font-weight: 500;
    font-size: 13.5px;
    line-height: 1.35;
  }
  .address { margin: 0 0 24px; }
  .contact-list { list-style: none; margin: 0; padding: 0; }
  .contact-list li {
    display: flex;
    align-items: center;
    gap: 8px;
    height: 21px;
  }
  .icon { width: 13px; height: 13px; flex: none; }
</style>
</head>
<body>
<main class="canvas">

  <section class="card card-front" aria-label="Card front">
    <p class="brand-name">Varko Works</p>
  </section>

  <section class="card card-back" aria-label="Card back">
    <svg class="wave" width="560" height="320" viewBox="0 0 560 320">
      <path d="M0,320 L0,300 C120,250 250,262 360,236 C460,212 530,150 560,70 L560,320 Z" fill="var(--red)"/>
      <path d="M0,300 C120,250 250,262 360,236 C460,212 530,150 560,70" fill="none" stroke="var(--navy)" stroke-width="4"/>
    </svg>

    <p class="brand-name">Varko Works</p>

    <div class="contact">
      <p class="address">18761 52nd Avenue<br>S, Kent, WA 98047</p>
      <ul class="contact-list">
        <li>
          <svg class="icon" viewBox="0 0 16 16" aria-hidden="true">
            <path d="M1 5 C1 2 15 2 15 5 L12 7 L10 5 L6 5 L4 7 Z" fill="var(--red)"/>
            <rect x="3" y="7" width="10" height="7" rx="1" fill="var(--red)"/>
          </svg>
          (253) 617-4930
        </li>
        <li>
          <svg class="icon" viewBox="0 0 16 16" aria-hidden="true">
            <rect x="1" y="3" width="14" height="10" fill="var(--red)"/>
            <path d="M1 3 L8 9 L15 3" fill="none" stroke="var(--white)" stroke-width="1.2"/>
          </svg>
          martin@plumlinegroup.com
        </li>
        <li>
          <svg class="icon" viewBox="0 0 16 16" aria-hidden="true">
            <circle cx="8" cy="8" r="7" fill="var(--red)"/>
            <path d="M1 8 H15 M8 1 C4 5 4 11 8 15 M8 1 C12 5 12 11 8 15" fill="none" stroke="var(--white)" stroke-width="1"/>
          </svg>
          www.varkoworks.com
        </li>
      </ul>
    </div>
  </section>

</main>
</body>
</html>
```